Business Cards - Brightpath Horizon

need to design unique business card for my mortgage business. I need to design credit card style business card for my business or any unique idea that you might have

Target Market(s)

Home Loan customers

Industry/Entity Type

Mortgage Brokerage

Contact Information for Business Card

please design credit card style or very unique style business card

Colors

Designer to choose colors to be used in the design.

Requirements
Must have
• Name
• position
• Phone number
• fax number
• email address
• website address
• social media address
• All above fields will be provided once design in finalised

```html
<!DOCTYPE html>
<html lang="en">
<head>
<meta charset="utf-8">
<title>Brightpath Horizon – Business Cards</title>
<link href="https://fonts.googleapis.com/css2?family=Montserrat:wght@400;500;600&display=swap" rel="stylesheet">
<style>
  :root {
    --stage: #ecebe8;
    --orange: #f28a22;
    --orange-light: #f6a043;
    --navy: #2f4aa0;
    --sky: #22a7e0;
    --ink: #3a3a3a;
    --white: #ffffff;
  }
  * { box-sizing: border-box; margin: 0; padding: 0; }
  html, body {
    width: 1200px; height: 930px; overflow: hidden;
    background: var(--stage);
    font-family: "Montserrat", sans-serif;
  }
  .stage { position: relative; width: 1200px; height: 930px; }

  .card {
    position: absolute;
    width: 580px; height: 330px;
    border-radius: 4px;
    overflow: hidden;
    box-shadow: 0 10px 24px rgba(0,0,0,.18);
  }

  /* Back of card */
  .card--back {
    left: 70px; top: 110px;
    background: linear-gradient(135deg, var(--orange-light), var(--orange) 55%);
    color: var(--white);
  }
  .card--back .brand-name {
    position: absolute; left: 0; right: 0; top: 126px;
    font-size: 32px; font-weight: 600; letter-spacing: 1px;
    color: var(--white);
    display: flex; align-items: center; justify-content: center; gap: 12px;
  }
  .card--back .brand-mark {
    width: 14px; height: 14px; border-radius: 50%; background: var(--white);
  }
  .card--back .website {
    position: absolute; bottom: 36px; left: 0; right: 0;
    text-align: center; font-size: 14px; letter-spacing: 1.5px;
  }

  /* Front of card */
  .card--front {
    left: 550px; top: 480px;
    background: var(--white);
  }
  .card--front .brand-name {
    position: absolute; left: 40px; top: 132px;
    width: 230px;
    font-size: 28px; line-height: 1.15; font-weight: 600;
    color: var(--navy);
  }
  .card--front .divider {
    position: absolute; left: 290px; top: 46px;
    width: 2px; height: 150px; background: var(--sky);
  }
  .contact {
    position: absolute; left: 314px; top: 40px; right: 16px;
    color: var(--ink);
  }
  .contact .person-name {
    font-size: 21px; font-weight: 500; letter-spacing: 2px;
    color: var(--sky); text-transform: uppercase;
  }
  .contact .role { font-size: 13px; font-weight: 600; margin-top: 2px; }
  .contact .address { font-size: 12px; line-height: 1.4; margin-top: 14px; }
  .contact .lines { list-style: none; margin-top: 14px; font-size: 12px; line-height: 1.5; }
  .contact .lines li { display: flex; align-items: center; gap: 8px; }
  .contact .lines svg { width: 10px; height: 10px; flex: none; }

  .card--front .waves { position: absolute; left: 0; bottom: 0; width: 580px; height: 150px; }
</style>
</head>
<body>
<main class="stage">

  <section class="card card--back">
    <div class="brand-name"><span class="brand-mark"></span>Brightpath Horizon</div>
    <div class="website">www.yourwebsite.com</div>
  </section>

  <section class="card card--front">
    <div class="brand-name">Brightpath Horizon</div>
    <div class="divider"></div>

    <div class="contact">
      <div class="person-name">Daniel Whitmore</div>
      <div class="role">Founder</div>
      <div class="address">480 Harbor View Rd.<br>Coral Bay, FL 33071</div>
      <ul class="lines">
        <li>
          <svg viewBox="0 0 10 10"><path d="M2 1l2 2-1 1.2a6 6 0 0 0 2.8 2.8L7 6l2 2-1.3 1.3C4.5 9 1 5.5.7 2.3z" fill="var(--sky)"/></svg>
          555-018-4420
        </li>
        <li>
          <svg viewBox="0 0 10 10"><rect x=".5" y="2" width="9" height="6" rx="1" fill="none" stroke="var(--sky)"/><path d="M.8 2.4L5 5.5l4.2-3.1" fill="none" stroke="var(--sky)"/></svg>
          hello@brightpathhorizon.com
        </li>
        <li>
          <svg viewBox="0 0 10 10"><circle cx="5" cy="5" r="4.3" fill="none" stroke="var(--sky)"/><ellipse cx="5" cy="5" rx="1.8" ry="4.3" fill="none" stroke="var(--sky)"/><path d="M.7 5h8.6" stroke="var(--sky)"/></svg>
          www.brightpathhorizon.com
        </li>
      </ul>
    </div>

    <svg class="waves" viewBox="0 0 580 150" preserveAspectRatio="none">
      <path d="M0 124 C90 100 170 92 250 88 C170 96 90 110 0 132Z" fill="var(--orange)"/>
      <path d="M230 93 C330 84 450 72 580 12 L580 22 C520 52 440 74 330 83 C290 86 260 89 230 93Z" fill="var(--sky)"/>
      <path d="M0 136 C120 110 230 96 330 90 C440 82 520 60 580 30 L580 150 L0 150Z" fill="var(--navy)"/>
    </svg>
  </section>

</main>
</body>
</html>
```